Form With Marla - Health and Wellness Business Card and Logo

I need a business card design with a logo for my business you can check out at www.formwithmarla.net. I want something more original, simplistic, and memorable than the basic logo I have on my site currently. I am a health and wellness coach and I offer mindset coaching and nutrition plans. I like the colour teal and dark grey/black for my theme colours. I emphasize growth, longterm change, and the whole package of "healthy mind, healthy body, healthy life". I had played around the idea of intertwining 3 M's or incorporating growth (leaves etc.) into my design. I want my expertise and experience to show through. In one glance I want people to understand with confidence I can help them accomplish anything they set their minds to. I look forward to seeing what everyone comes up with!

Industry/Entity Type

Health And Wellness

Contact Information for Business Card

Form With Marla
Marla Prentiss
BSc, Health & Wellness Coach
"Manifest your best"
www.formwithmarla.net
formwithmarla@quillpost.net
472-618-9043

Colors
33b8a4
ffffff
333333
000000

Requirements
Must have
• A memorable and unique logo for my business!
Nice to have
• Could have the phrase "Are you unhappy with your body and state of health?" or "It takes the right skills to develop habits in order to create long term change. I can help you get there."

```html
<!DOCTYPE html>
<html lang="en">
<head>
<meta charset="utf-8">
<title>Form With Marla — Business Card</title>
<link rel="stylesheet" href="https://fonts.googleapis.com/css2?family=Exo+2:wght@700&family=Open+Sans:wght@400;700&display=swap">
<style>
  :root {
    --backdrop: #2a2a2a;
    --card: #222222;
    --teal: #1a9c90;
    --teal-bright: #33b8a4;
    --white: #ffffff;
    --soft-white: #e6e6e6;
  }
  * { box-sizing: border-box; margin: 0; padding: 0; }
  html, body {
    width: 1200px; height: 1000px; overflow: hidden;
    background: var(--backdrop);
  }
  .canvas { position: relative; width: 1200px; height: 1000px; }
  .card {
    position: absolute; left: 220px; width: 760px; height: 434px;
    background: var(--card);
    box-shadow: 0 14px 30px rgba(0,0,0,.45);
  }
  .card--front { top: 40px; }
  .card--back { top: 520px; }

  .brand-mark {
    position: absolute; left: 50%; top: 105px; transform: translateX(-50%);
    width: 150px; height: 150px;
  }
  .brand-name {
    position: absolute; left: 0; right: 0; top: 300px; text-align: center;
    font-family: "Open Sans", sans-serif; font-weight: 700;
    font-size: 24px; letter-spacing: 3px; color: var(--teal);
  }

  .identity { position: absolute; left: 60px; top: 62px; }
  .identity__name {
    font-family: "Exo 2", sans-serif; font-weight: 700;
    font-size: 27px; letter-spacing: .5px; color: var(--white);
  }
  .identity__role {
    font-family: "Open Sans", sans-serif; font-size: 19px; color: var(--teal);
    margin-top: 2px;
  }
  .tagline {
    position: absolute; left: 60px; top: 196px;
    font-family: "Open Sans", sans-serif; font-size: 17px; line-height: 1.4;
    color: var(--soft-white); letter-spacing: .4px;
  }
  .contacts {
    position: absolute; left: 34px; top: 268px; list-style: none;
    font-family: "Open Sans", sans-serif; font-size: 18px; color: var(--soft-white);
    letter-spacing: .3px;
  }
  .contacts li { display: flex; align-items: center; gap: 12px; height: 30px; }
  .contacts svg { width: 15px; height: 15px; fill: var(--teal); flex: none; }
  .contacts .accent { color: var(--teal); }

  .corner-mark {
    position: absolute; right: 70px; bottom: 70px; width: 130px; height: 130px;
  }
</style>
</head>
<body>
<main class="canvas">
  <section class="card card--front" aria-label="Card front">
    <svg class="brand-mark" viewBox="0 0 150 150" aria-hidden="true">
      <circle cx="75" cy="75" r="70" fill="none" stroke="var(--teal)" stroke-width="4"/>
    </svg>
    <p class="brand-name">formwithmarla</p>
  </section>

  <section class="card card--back" aria-label="Card back">
    <div class="identity">
      <h1 class="identity__name">MARLA PRENTISS</h1>
      <p class="identity__role">BSc, Health &amp; Wellness Coach</p>
    </div>
    <p class="tagline">“Manifest your best”</p>
    <ul class="contacts">
      <li>
        <svg viewBox="0 0 16 16" aria-hidden="true"><path d="M3.6 1.2l2.2 2.6c.3.4.3.9 0 1.3L4.7 6.3c.8 1.8 2.2 3.2 4 4l1.2-1.1c.4-.3.9-.3 1.3 0l2.6 2.2c.4.3.4.9.1 1.3l-1.2 1.5c-.4.4-1 .6-1.6.4C6 13.3 2.7 10 1.4 5c-.2-.6 0-1.2.4-1.6L3.3 1.1c.1 0 .2 0 .3.1z"/></svg>
        <span>472-618-9043</span>
      </li>
      <li>
        <svg viewBox="0 0 16 16" aria-hidden="true"><path d="M1 3h14v10H1z M2 4l6 5 6-5" stroke="var(--card)" stroke-width="1.2"/></svg>
        <span>formwithmarla@quillpost.net</span>
      </li>
      <li>
        <svg viewBox="0 0 16 16" aria-hidden="true"><circle cx="8" cy="8" r="7"/><path d="M1 8h14M8 1c-3 3-3 11 0 14M8 1c3 3 3 11 0 14" stroke="var(--card)" stroke-width="1" fill="none"/></svg>
        <span>www.<span class="accent">formwithmarla</span>.net</span>
      </li>
    </ul>
    <svg class="corner-mark" viewBox="0 0 130 130" aria-hidden="true">
      <circle cx="65" cy="65" r="60" fill="none" stroke="var(--teal)" stroke-width="4"/>
    </svg>
  </section>
</main>
</body>
</html>
```